Food broker, trader, wholesaler, liquidator looking for a 5 pages website

Looking for a 5 pages website design. We are food brokers, traders, wholesaler and closeout buyer working with manufacturers, distributors, importers sell to retailers, food service operators and industrial (ingredients). We help market their products. We are a resource for those who need a solution in the distribution/selling/placement of food on the shelves, kitchens and pantries. Whether we open new accounts with new products or sell short dated inventory, we know where to go and get results.

Target Market(s)

Food manufacturers, food distributors, food brokers

Coding

Coded - Design and coding required

Number of Pages Required

4 page

Font styles to use
Serif

Requirements
Must have
• Food-food production-warehouse-Food packaging-people meeting-trucks-supermarket shelves-

```html
<!DOCTYPE html>
<html lang="en">
<head>
<meta charset="utf-8">
<title>Harbor Provision Co.</title>
<link rel="stylesheet" href="https://fonts.googleapis.com/css2?family=Montserrat:wght@400;500;600;800&family=Oswald:wght@300&family=Raleway:wght@400;500&display=swap">
<style>
:root{
  --navy:#101467;
  --navy-deep:#0b0d28;
  --sea:#1d3a7a;
  --sea-dark:#142a5e;
  --bright:#0b2cff;
  --ink:#1a1a1a;
  --grey-band:#ececec;
  --white:#ffffff;
  --muted:#cfd3ea;
}
*{margin:0;padding:0;box-sizing:border-box}
html,body{width:1200px;height:3932px;overflow:hidden}
body{position:relative;background:var(--white);font-family:"Montserrat",sans-serif;color:var(--ink)}
.abs{position:absolute}
h1,h2,h3{font-weight:400}
/* hero */
.hero{left:0;top:0;width:1200px;height:600px;background:linear-gradient(180deg,var(--sea-dark) 0%,var(--sea) 50%,#24488c 80%,#ffffff 100%)}
.hero-photo{left:0;top:0;width:1200px;height:600px;background:radial-gradient(ellipse 360px 90px at 640px 240px,rgba(160,120,110,.35),transparent 70%)}
.topbar{left:0;top:0;width:1200px;height:34px;border-bottom:1px solid rgba(255,255,255,.25);color:var(--white);font-size:11px;font-family:"Raleway",sans-serif}
.topbar .call{left:113px;top:8px;display:flex;gap:6px;align-items:center}
.topbar .mail{right:120px;top:8px;display:flex;gap:6px;align-items:center}
.brand{left:113px;top:44px;display:flex;align-items:center;gap:12px}
.brand .mark{width:80px;height:56px;border-radius:50%;background:var(--navy);border:2px solid var(--white)}
.brand span{color:var(--white);font-weight:600;font-size:11px;letter-spacing:.5px;text-transform:uppercase}
.nav{right:112px;top:66px;display:flex;gap:34px;font-family:"Raleway",sans-serif;font-size:15px;color:var(--white);letter-spacing:1px}
.nav .on{border-bottom:4px solid var(--white);padding-bottom:6px}
.hero-title{left:0;top:212px;width:1200px;text-align:center;color:var(--white);font-family:"Oswald",sans-serif;font-weight:300;font-size:46px;line-height:56px}
.hero-sub{left:0;top:272px;width:1200px;text-align:center;color:var(--white);font-family:"Raleway",sans-serif;font-size:17px}
.btn{top:322px;height:40px;border-radius:20px;font-family:"Raleway",sans-serif;font-size:14px;letter-spacing:2px;display:flex;align-items:center;justify-content:center}
.btn.read{left:433px;width:147px;background:var(--bright);color:var(--white)}
.btn.quote{left:593px;width:162px;background:var(--white);color:var(--ink)}
.dots{left:552px;top:386px;display:flex;gap:4px}
.dots i{width:11px;height:11px;border-radius:50%;background:var(--white);display:block}
.dots i:first-child{background:transparent;border:1.5px solid var(--white)}
/* intro */
.intro-title{left:0;top:676px;width:1200px;text-align:center;color:var(--navy);font-size:25px;font-weight:500}
.intro-text{left:240px;top:740px;width:720px;text-align:center;font-size:14.5px;line-height:23px}
.more-link{left:0;top:874px;width:1200px;text-align:center;font-size:10px;letter-spacing:3px;color:var(--navy)}
.more-link span{border-bottom:2px solid var(--navy);padding-bottom:2px}
.warehouse{left:0;top:962px;width:1200px;height:583px;background:linear-gradient(90deg,#8a6a48 0%,#c9a071 25%,#6f7a86 45%,#c08c5c 65%,#7d9a56 100%)}
/* what we do */
.section-title{left:0;width:1200px;text-align:center;color:var(--navy);font-size:23px;font-weight:500;letter-spacing:.5px}
.service{top:1713px;width:300px;height:267px;background:var(--navy);color:var(--white);text-align:center;box-shadow:0 4px 14px rgba(0,0,0,.12)}
.service svg{margin-top:48px}
.service h3{font-size:14px;font-weight:600;margin-top:20px;letter-spacing:.5px}
.service p{font-size:14px;color:var(--muted);line-height:20px;width:210px;margin:4px auto 0}
.pride{left:260px;top:2062px;width:680px;text-align:center;font-size:18px;line-height:29px;color:var(--ink)}
.welcome{left:0;top:2202px;width:1200px;text-align:center;font-size:23px;color:var(--navy)}
/* featured */
.product{top:2413px;width:238px;height:362px;background:var(--navy);overflow:hidden;color:var(--white);text-align:center}
.product .pic{position:absolute;left:0;top:0;width:238px;height:190px}
.product .cut{position:absolute;left:0;top:150px}
.product .badge{position:absolute;left:86px;top:132px;width:66px;height:66px;border-radius:50%;background:var(--white);display:flex;align-items:center;justify-content:center}
.product h3{position:absolute;left:0;top:212px;width:238px;font-size:25px;font-weight:800;line-height:25px;letter-spacing:.5px}
.product p{position:absolute;left:28px;width:182px;font-size:12.5px;line-height:18px;color:var(--muted)}
.product .fade{position:absolute;left:0;bottom:0;width:238px;height:40px;background:linear-gradient(180deg,rgba(255,255,255,0),rgba(255,255,255,.85))}
/* people say */
.people{left:0;top:2855px;width:1200px;height:604px;background:var(--grey-band)}
.people-title{left:0;top:2900px;width:1200px;text-align:center;font-family:"Raleway",sans-serif;font-size:36px;font-weight:400;color:#222}
.avatar{border-radius:50%;background:linear-gradient(160deg,#c9c9c9,#8d8d8d)}
.quote-mark{left:262px;top:3022px}
.quote-text{left:320px;top:3070px;width:560px;text-align:center;font-size:14px;line-height:22.5px;font-style:italic;color:#222}
.quote-name{left:0;top:3186px;width:1200px;text-align:center;font-size:13px;font-style:italic;letter-spacing:1.5px}
.quote-name span{border-bottom:1px solid #444;padding:0 6px 6px}
/* contact */
.footer{left:0;top:3459px;width:1200px;height:473px;background:var(--navy-deep)}
.contact-frame{left:243px;top:3248px;width:714px;height:266px;background:var(--navy-deep)}
.contact-box{left:267px;top:3272px;width:666px;height:237px;background:var(--white)}
.contact-box h2{position:absolute;left:0;top:34px;width:666px;text-align:center;font-size:18px;font-weight:500}
.field{position:absolute;border:1px solid #999;font-size:9.5px;letter-spacing:1px;padding:10px 10px;color:#333}
.submit{position:absolute;left:332px;top:156px;width:280px;height:36px;background:var(--bright);color:var(--white);font-size:11px;display:flex;align-items:center;justify-content:center}
/* footer */
.f-brand{left:113px;top:3581px;width:128px;height:92px;border-radius:50%;background:var(--navy);border:2px solid var(--white)}
.f-name{left:113px;top:3682px;color:var(--white);font-size:12px;font-weight:600}
.f-about{left:113px;top:3706px;width:200px;color:var(--white);font-size:12px;line-height:17px}
.f-head{top:3582px;color:var(--white);font-size:12.5px;letter-spacing:1px}
.f-links{left:389px;top:3618px;color:var(--white);font-size:12px;line-height:28.5px}
.f-contact{left:565px;top:3616px;color:var(--white);font-size:11.5px;line-height:18px}
.f-contact div{display:flex;gap:10px;margin-bottom:16px}
.f-email{left:840px;top:3618px;width:248px;height:36px;background:var(--white);border:1px solid #ccc;font-size:13px;color:#888;padding:9px 16px}
.f-sub{left:840px;top:3662px;width:248px;height:36px;background:var(--bright);color:var(--white);font-size:12px;display:flex;align-items:center;justify-content:center}
.social{top:3721px;width:40px;height:40px;border-radius:50%;border:2px solid var(--white)}
.copy{left:0;top:3822px;width:1200px;text-align:center;color:var(--white);font-size:13px;font-weight:600}
.copy b{color:#3d5bff;font-weight:600}
</style>
</head>
<body>

<div class="abs hero"></div>
<div class="abs hero-photo" role="img" aria-label="Aerial photo of a container ship crossing open sea"></div>

<div class="abs topbar">
  <div class="abs call">
    <svg width="12" height="12" viewBox="0 0 24 24" fill="none" stroke="#fff" stroke-width="2"><path d="M5 3h4l2 5-3 2a12 12 0 006 6l2-3 5 2v4a2 2 0 01-2 2A17 17 0 013 5a2 2 0 012-2z"/></svg>
    Call Us : 070-5310-2264
  </div>
  <div class="abs mail">
    <svg width="16" height="12" viewBox="0 0 24 18" fill="#fff"><path d="M0 8 L24 0 L18 18 L11 12 Z"/></svg>
    Email : hello@harborprovision.example
  </div>
</div>

<div class="abs brand"><div class="mark"></div><span>Harbor Provision Co.</span></div>
<nav class="abs nav">
  <span class="on">Home</span><span>About US</span><span>What we do</span><span>Contact</span><span>Giving Back</span>
</nav>

<h1 class="abs hero-title">Harbor Provision works with food manufacturers,</h1>
<p class="abs hero-sub">brand owners, distributors and wholesalers market their products.</p>
<div class="abs btn read">Read More</div>
<div class="abs btn quote">Free quote</div>
<div class="abs dots"><i></i><i></i><i></i><i></i></div>

<h2 class="abs intro-title">Retail, Food Service and Industrial ingredients.</h2>
<p class="abs intro-text">Retail, Food Service and Industrial ingredients.<br>Founded in 2008, Harbor Provision started with the distribution of gluten free products understanding the need to provide access to unique flavors and products for the celiac consumers. From this, we expanded into deli, dairy, groceries, frozen and beverages.</p>
<div class="abs more-link"><span>READ MORE</span></div>

<div class="abs warehouse" role="img" aria-label="Photo of a wholesale warehouse aisle with stacked food pallets and a shopping cart"></div>

<h2 class="abs section-title" style="top:1652px">WHAT WE DO</h2>

<div class="abs service" style="left:113px">
  <svg width="52" height="52" viewBox="0 0 52 52" fill="none" stroke="#fff" stroke-width="2"><rect x="4" y="6" width="44" height="28"/><path d="M26 34v12M18 46h16M26 12l3 7h7l-6 4 2 7-6-4-6 4 2-7-6-4h7z"/></svg>
  <h3>Sales &amp; Marketing:</h3>
  <p>we connect food buyers and sellers through a dedicated approach.</p>
</div>
<div class="abs service" style="left:450px">
  <svg width="56" height="52" viewBox="0 0 56 52" fill="none" stroke="#fff" stroke-width="2"><path d="M20 4v20M14 18l6 6 6-6M34 24V4M28 10l6-6 6 6M4 36h18l10 4h14l6 6H16l-12-4"/></svg>
  <h3>Trading</h3>
  <p>we connect food buyers and sellers through a dedicated approach.</p>
</div>
<div class="abs service" style="left:786px">
  <svg width="52" height="52" viewBox="0 0 52 52" fill="none" stroke="#fff" stroke-width="2"><path d="M4 48V18L26 4l22 14v30z"/><rect x="14" y="30" width="10" height="10"/><rect x="28" y="30" width="10" height="10"/><rect x="21" y="20" width="10" height="10"/></svg>
  <h3>Closeout/Excess Inventory</h3>
  <p>we connect food buyers and sellers through a dedicated approach.</p>
</div>

<p class="abs pride">We pride ourselves in working in an easy, personal and accessible environment making our customers and vendors comfortable with us. We look forward to connecting with you and evaluating how we can assist you reaching your sales objectives.</p>
<p class="abs welcome">Welcome and thank you for visiting harborprovision.example</p>

<h2 class="abs section-title" style="top:2352px">FEATURED PRODUCTS</h2>

<div class="abs product" style="left:113px">
  <div class="pic" role="img" aria-label="Photo of a deli sandwich on a board" style="background:linear-gradient(160deg,#5b3b26,#c98a4d 55%,#3a2516)"></div>
  <svg class="cut" width="238" height="60"><path d="M0 60 L238 0 L238 60 Z" fill="#101467"/></svg>
  <div class="badge"><svg width="34" height="34" viewBox="0 0 34 34" fill="none" stroke="#101467" stroke-width="2"><circle cx="17" cy="17" r="13"/><path d="M9 22 L24 10"/></svg></div>
  <h3>DELI</h3>
  <p style="top:252px">Founded in 2008, Harbor Provision started with the distribution.</p>
  <div class="fade"></div>
</div>
<div class="abs product" style="left:357px">
  <div class="pic" role="img" aria-label="Photo of nuts in bowls beside wrapped dairy jars" style="background:linear-gradient(160deg,#8a7766,#d8cbbd 55%,#6d5a4a)"></div>
  <svg class="cut" width="238" height="60"><path d="M0 60 L238 0 L238 60 Z" fill="#101467"/></svg>
  <div class="badge"><svg width="34" height="34" viewBox="0 0 34 34" fill="none" stroke="#101467" stroke-width="2"><path d="M12 6h8v5l4 5v14H10V16l2-5z"/></svg></div>
  <h3>DAIRY</h3>
  <p style="top:252px">Founded in 2008, Harbor Provision started with the distribution.</p>
  <div class="fade"></div>
</div>
<div class="abs product" style="left:602px">
  <div class="pic" role="img" aria-label="Photo of a crate of fresh vegetables and groceries" style="background:linear-gradient(160deg,#3f8a3c,#e0b030 50%,#c23a2a)"></div>
  <svg class="cut" width="238" height="60"><path d="M0 60 L238 0 L238 60 Z" fill="#101467"/></svg>
  <div class="badge"><svg width="34" height="34" viewBox="0 0 34 34" fill="none" stroke="#101467" stroke-width="2"><rect x="6" y="14" width="22" height="14"/><path d="M10 14V8M16 14V6M22 14V9"/></svg></div>
  <h3>GROCERIES</h3>
  <p style="top:252px">Founded in 2008, Harbor Provision started with the distribution.</p>
  <div class="fade"></div>
</div>
<div class="abs product" style="left:846px">
  <div class="pic" role="img" aria-label="Photo of colourful frozen cocktails on a dark background" style="background:linear-gradient(160deg,#1a1a1a,#e0552a 50%,#2a1a14)"></div>
  <svg class="cut" width="238" height="60"><path d="M0 60 L238 0 L238 60 Z" fill="#101467"/></svg>
  <div class="badge"><svg width="34" height="34" viewBox="0 0 34 34" fill="none" stroke="#101467" stroke-width="2"><path d="M8 10h18l-3 20H11zM18 10l4-6"/></svg></div>
  <h3>FROZEN AND<br>BEVERAGES</h3>
  <p style="top:276px">Founded in 2008, Harbor Provision started with the distribution.</p>
  <div class="fade"></div>
</div>

<div class="abs people"></div>
<h2 class="abs people-title">People Say</h2>
<svg class="abs" style="left:456px;top:2994px" width="16" height="24" viewBox="0 0 16 24" fill="none" stroke="#888" stroke-width="2.5"><path d="M12 3 L4 12 L12 21"/></svg>
<div class="abs avatar" style="left:488px;top:2982px;width:46px;height:46px" role="img" aria-label="Customer portrait"></div>
<div class="abs avatar" style="left:560px;top:2960px;width:82px;height:82px;border:4px solid #fff" role="img" aria-label="Featured customer portrait"></div>
<div class="abs avatar" style="left:670px;top:2982px;width:46px;height:46px" role="img" aria-label="Customer portrait"></div>
<svg class="abs" style="left:734px;top:2994px" width="16" height="24" viewBox="0 0 16 24" fill="none" stroke="#888" stroke-width="2.5"><path d="M4 3 L12 12 L4 21"/></svg>
<svg class="abs quote-mark" width="170" height="150" viewBox="0 0 170 150" aria-hidden="true"><path d="M0 0h70v80l-25 70H10l20-70H0zM90 0h70v80l-25 70h-35l20-70H90z" fill="#d8d8d8"/></svg>
<p class="abs quote-text">Lorem Ipsum is simply dummy text of the printing and typesetting industry. Lorem Ipsum has been the industry's standard dummy text ever since the 1500s, when an unknown printer took a galley of type and scrambled it to make a type specimen book.</p>
<div class="abs quote-name"><span>Alma Reyes</span></div>

<div class="abs footer"></div>
<div class="abs contact-frame"></div>
<div class="abs contact-box">
  <h2>GET IN IN TOUCH</h2>
  <div class="field" style="left:46px;top:72px;width:280px;height:36px">NAME:</div>
  <div class="field" style="left:46px;top:114px;width:280px;height:36px">EMAIL:</div>
  <div class="field" style="left:46px;top:156px;width:280px;height:36px">PHONE:</div>
  <div class="field" style="left:332px;top:72px;width:280px;height:78px">COMMENTS :</div>
  <div class="submit">SUBMIT NOW</div>
</div>

<div class="abs f-brand"></div>
<div class="abs f-name">Harbor Provision Co.</div>
<p class="abs f-about">Lorem Ipsum is simply dummy text of the printing and typesetting industry.</p>

<div class="abs f-head" style="left:389px">SITEMAP</div>
<div class="abs f-links">Home<br>About US<br>What we do<br>Contact<br>Giving Back</div>

<div class="abs f-head" style="left:567px">GET IN TOUCH</div>
<div class="abs f-contact">
  <div><svg width="14" height="18" viewBox="0 0 14 18" fill="#2f4dff"><path d="M7 0a7 7 0 017 7c0 5-7 11-7 11S0 12 0 7a7 7 0 017-7z"/><circle cx="7" cy="7" r="2.5" fill="#0b0d28"/></svg><span>418 Cedar Row, 3rd Floor<br>Brookfield, CA 95012 USA</span></div>
  <div><svg width="14" height="14" viewBox="0 0 24 24" fill="none" stroke="#2f4dff" stroke-width="2"><path d="M5 3h4l2 5-3 2a12 12 0 006 6l2-3 5 2v4a2 2 0 01-2 2A17 17 0 013 5a2 2 0 012-2z"/></svg><span>(+800) 555 019 42</span></div>
  <div><svg width="16" height="12" viewBox="0 0 24 18" fill="#2f4dff"><path d="M0 8 L24 0 L18 18 L11 12 Z"/></svg><span>info@harborprovision.example</span></div>
</div>

<div class="abs f-head" style="left:838px">NEWSLETTER SUBSCRIBE</div>
<div class="abs f-email">Enter your email id :</div>
<div class="abs f-sub">NEWSLETTER SUBSCRIBE</div>
<div class="abs social" style="left:840px;background:#3b5998" role="img" aria-label="Social link"></div>
<div class="abs social" style="left:886px;background:#2a8fd8" role="img" aria-label="Social link"></div>
<div class="abs social" style="left:932px;background:#1a6fb0" role="img" aria-label="Social link"></div>
<div class="abs social" style="left:978px;background:#d7262a" role="img" aria-label="Social link"></div>

<p class="abs copy">Copyright © 2020 <b>Harbor Provision Co.</b></p>

</body>
</html>
```